School Hallway Magnetic Display Design for school values

I am looking for a someone to help me design a magnetic hallway display that will hang in the hallway of our small school. There are several elements, including 1. 6ft by 4ft designed magnetic bulletin board, 2. Magnets that will stick to the board. See attachment for which elements belong where. The display will be for our MOBLAT program, which rewards students for demonstrating our school values. We want the display to be beautiful and interactive. We are also rebranding, so we want the design to align with our new fonts and colors. In the attached PDF is an outline of our new brand guidelines. Unfortunately, we don't have the color codes, but I'm hoping that you can match the colors listed. Attached are elements to be used on the board, but please use your creativity to make it more dynamic and visually appealing. For example, the star magnets could be another shape. The MOBLAT magnets must remain the same. I've included two photos of boards at other schools that inspired this project.

Target Market(s)

School Community

Industry/Entity Type

Education

Requirements
Should not have
• School Logo

```html
<!DOCTYPE html>
<html lang="en">
<head>
<meta charset="utf-8">
<title>MOBLAT at HVS – Hallway Values Display</title>
<link rel="stylesheet" href="https://fonts.googleapis.com/css2?family=Fraunces:opsz,wght@9..144,700;9..144,800&display=swap">
<style>
  :root {
    --backdrop: #4f4f4f;
    --board: #ffffff;
    --coral: #df8a73;
    --lilac: #bd9bc3;
    --sage: #d8dfbb;
    --sun: #fdd882;
    --sky: #b0cde2;
    --navy: #2b5c95;
    --ink-navy: #234e76;
    --star: #fdd77a;
    --shadow: drop-shadow(14px 14px 12px rgba(0,0,0,0.45));
  }
  * { margin: 0; padding: 0; box-sizing: border-box; }
  html, body { width: 1200px; height: 3200px; overflow: hidden; }
  body { background: var(--backdrop); position: relative; font-family: "Fraunces", Georgia, serif; }

  .board {
    position: absolute; left: 133px; top: 89px; width: 934px; height: 621px;
    background: var(--board); overflow: hidden;
    box-shadow: 16px 16px 16px rgba(0,0,0,0.45);
  }
  .board-ornament {
    position: absolute; left: 0; top: 0; width: 193px; height: 100%;
    background: linear-gradient(180deg, var(--sun) 0%, var(--ink-navy) 30%, var(--ink-navy) 55%, var(--sun) 72%, var(--ink-navy) 100%);
    border-top-right-radius: 40px; border-bottom-right-radius: 40px;
  }
  .board-title {
    position: absolute; left: 163px; top: 58px;
    font-size: 64px; font-weight: 800; letter-spacing: -1px; white-space: nowrap;
    line-height: 1;
  }
  .board-title .program { color: var(--coral); }
  .board-title .joiner { color: var(--lilac); }
  .board-title .school { color: var(--sky); }
  .thermometer { position: absolute; left: 716px; top: 40px; width: 170px; height: 545px; }

  .value-magnet {
    position: absolute; width: 283px; height: 848px; border-radius: 142px;
    overflow: hidden;
    display: flex; align-items: flex-start; justify-content: center;
    box-shadow: 16px 16px 16px rgba(0,0,0,0.45);
  }
  .value-magnet span {
    position: relative; z-index: 1;
    color: #fff; font-size: 40px; font-weight: 700; letter-spacing: 0.5px; line-height: 1.2;
  }
  .value-magnet .magnet-motif {
    position: absolute; left: 0; right: 0; bottom: 0; height: 146px;
    background: linear-gradient(180deg, rgba(255,255,255,0.22), rgba(255,255,255,0.14));
  }
  .stewardship .magnet-motif { background: linear-gradient(180deg, rgba(255,255,255,0.3), rgba(255,255,255,0.2)); }

  .row-1 { top: 838px; }
  .row-2 { top: 1735px; }
  .col-1 { left: 143px; } .col-2 { left: 456px; } .col-3 { left: 774px; }
  .simplicity { background: var(--coral); } .simplicity span { margin-top: 354px; }
  .peace { background: var(--lilac); } .peace span { margin-top: 370px; }
  .integrity { background: var(--sage); } .integrity span { margin-top: 367px; }
  .community { background: var(--sun); } .community span { margin-top: 365px; }
  .equality { background: var(--sky); } .equality span { margin-top: 370px; }
  .stewardship { background: var(--navy); } .stewardship span { margin-top: 366px; }

  .star-magnet { position: absolute; width: 156px; height: 156px; filter: var(--shadow); }
</style>
</head>
<body>
  <section class="board">
    <div class="board-ornament" role="img" aria-label="Decorative leaves and concentric sun arcs in navy, yellow and coral"></div>
    <h1 class="board-title"><span class="program">MOBLAT</span> <span class="joiner">at</span> <span class="school">HVS</span></h1>
    <svg class="thermometer" viewBox="0 0 170 545" aria-label="Progress thermometer">
      <path d="M55 40 a30 30 0 0 1 60 0 V388 a80 80 0 1 1 -60 0 Z" fill="#fff" stroke="var(--ink-navy)" stroke-width="5"/>
      <path d="M72 45 a13 13 0 0 1 26 0 V420 a52 52 0 1 1 -26 0 Z" fill="#fff" stroke="var(--ink-navy)" stroke-width="3"/>
      <g stroke="var(--ink-navy)" stroke-width="1.5">
        <line x1="72" y1="100" x2="86" y2="100"/><line x1="72" y1="115" x2="80" y2="115"/>
        <line x1="72" y1="130" x2="80" y2="130"/><line x1="72" y1="145" x2="80" y2="145"/>
        <line x1="72" y1="160" x2="86" y2="160"/><line x1="72" y1="175" x2="80" y2="175"/>
        <line x1="72" y1="190" x2="80" y2="190"/><line x1="72" y1="205" x2="80" y2="205"/>
        <line x1="72" y1="220" x2="86" y2="220"/><line x1="72" y1="235" x2="80" y2="235"/>
        <line x1="72" y1="250" x2="80" y2="250"/><line x1="72" y1="265" x2="80" y2="265"/>
        <line x1="72" y1="280" x2="86" y2="280"/><line x1="72" y1="295" x2="80" y2="295"/>
        <line x1="72" y1="310" x2="80" y2="310"/><line x1="72" y1="325" x2="80" y2="325"/>
        <line x1="72" y1="340" x2="86" y2="340"/><line x1="72" y1="355" x2="80" y2="355"/>
        <line x1="72" y1="370" x2="80" y2="370"/><line x1="72" y1="385" x2="86" y2="385"/>
      </g>
    </svg>
  </section>

  <div class="value-magnet simplicity row-1 col-1"><span>Simplicity</span><div class="magnet-motif" role="img" aria-label="Light leaf sprout motif"></div></div>
  <div class="value-magnet peace row-1 col-2"><span>Peace</span><div class="magnet-motif" role="img" aria-label="Light leaf sprout motif"></div></div>
  <div class="value-magnet integrity row-1 col-3"><span>Integrity</span><div class="magnet-motif" role="img" aria-label="Light leaf sprout motif"></div></div>
  <div class="value-magnet community row-2 col-1"><span>Community</span><div class="magnet-motif" role="img" aria-label="Light leaf sprout motif"></div></div>
  <div class="value-magnet equality row-2 col-2"><span>Equality</span><div class="magnet-motif" role="img" aria-label="Light leaf sprout motif"></div></div>
  <div class="value-magnet stewardship row-2 col-3"><span>Stewardship</span><div class="magnet-motif" role="img" aria-label="Light leaf sprout motif"></div></div>

  <svg width="0" height="0" style="position:absolute">
    <defs>
      <path id="star-shape" d="M75 8 Q80 8 83 15 L97 46 L131 50 Q142 52 136 62 L110 86 L118 121 Q120 132 109 128 L75 110 L41 128 Q30 132 32 121 L40 86 L14 62 Q8 52 19 50 L53 46 L67 15 Q70 8 75 8 Z" fill="var(--star)"/>
    </defs>
  </svg>
  <svg class="star-magnet" style="left:355px;top:2725px" viewBox="0 0 150 150"><use href="#star-shape"/></svg>
  <svg class="star-magnet" style="left:520px;top:2725px" viewBox="0 0 150 150"><use href="#star-shape"/></svg>
  <svg class="star-magnet" style="left:684px;top:2725px" viewBox="0 0 150 150"><use href="#star-shape"/></svg>
  <svg class="star-magnet" style="left:355px;top:2892px" viewBox="0 0 150 150"><use href="#star-shape"/></svg>
  <svg class="star-magnet" style="left:520px;top:2892px" viewBox="0 0 150 150"><use href="#star-shape"/></svg>
  <svg class="star-magnet" style="left:684px;top:2892px" viewBox="0 0 150 150"><use href="#star-shape"/></svg>
</body>
</html>
```